Business Card Design

We need the business card for our new business based in St. Marys, we manufacture mainly bubble wraps. And we would like the design to use our company logo and also make it easy for people to understand right away we are bubble wrap manufacturer

Industry/Entity Type

Business

Contact Information for Business Card

Cushtane Pty Ltd, 14 Larkin Road Kellwood NSW 2791, Tel: 02 9471 5826, Fax: 9471 5839, Dara Oyelaran, General Manager, Mobile :0438 217 564, dara.oyelaran@cushtane.com.au, Website: cushtane.com.au

```html
<!DOCTYPE html>
<html lang="en">
<head>
<meta charset="utf-8">
<title>Cushtane Pty Ltd — Business Card</title>
<link rel="stylesheet" href="https://fonts.googleapis.com/css2?family=Arimo:wght@400;700&display=swap">
<style>
  :root {
    --page-bg: #ecebe8;
    --front-light: #c9c9c9;
    --front-dark: #6e6e6e;
    --white: #ffffff;
    --card-white: #fbfbfb;
    --card-shade: #e6e6e6;
    --brand-red: #c4202b;
    --band-red: #b71c27;
    --ink-grey: #6a6a6a;
    --ink-dark: #4a4a4a;
    --logo-grey: #707070;
  }
  * { box-sizing: border-box; margin: 0; padding: 0; }
  html, body {
    width: 1200px; height: 885px; overflow: hidden;
    background: var(--page-bg);
    font-family: "Arimo", Arial, sans-serif;
  }
  .canvas { position: relative; width: 1200px; height: 885px; }

  .card { position: absolute; box-shadow: 0 6px 18px rgba(0,0,0,.18); }

  /* Front */
  .card-front {
    left: 120px; top: 282px; width: 560px; height: 320px;
    background: radial-gradient(ellipse at 55% 40%, var(--front-light) 0%, #a4a4a4 55%, var(--front-dark) 100%);
    display: flex; flex-direction: column; align-items: center; justify-content: center;
  }
  .front-logo {
    font-weight: 700; font-size: 74px; letter-spacing: 2px;
    color: var(--white); line-height: 1;
  }
  .front-tagline {
    margin-top: 14px; font-size: 15px; letter-spacing: 6.5px;
    color: var(--white); font-weight: 400;
  }

  /* Back */
  .card-back {
    left: 760px; top: 162px; width: 320px; height: 560px;
    background: linear-gradient(160deg, var(--white) 0%, var(--card-white) 50%, var(--card-shade) 100%);
    display: flex; flex-direction: column; align-items: center;
  }
  .back-logo {
    margin-top: 44px; font-weight: 700; font-size: 40px; letter-spacing: 1px;
    color: var(--logo-grey); line-height: 1;
  }
  .back-tagline {
    margin-top: 8px; font-size: 8.5px; letter-spacing: 3.4px; color: var(--ink-grey);
  }
  .company-name {
    margin-top: 52px; font-size: 27px; color: var(--brand-red); font-weight: 400;
  }
  .person-name {
    margin-top: 40px; font-size: 26px; color: var(--brand-red); font-weight: 700; line-height: 1;
  }
  .person-title { margin-top: 4px; font-size: 18px; color: var(--ink-grey); }

  .contact-lines { margin-top: 40px; list-style: none; }
  .contact-lines li {
    display: flex; align-items: center; gap: 10px;
    font-size: 17px; color: var(--ink-dark); line-height: 24px;
  }
  .contact-lines svg { width: 18px; height: 18px; fill: var(--brand-red); flex: none; }

  .email, .address {
    font-size: 14px; color: var(--ink-dark); text-align: center;
  }
  .email { margin-top: 26px; }
  .address { margin-top: 4px; }

  .web-band {
    position: absolute; left: 0; right: 0; bottom: 0; height: 74px;
    background: var(--band-red);
    display: flex; align-items: center; justify-content: center;
    color: var(--white); font-size: 27px; letter-spacing: .5px;
  }
</style>
</head>
<body>
<main class="canvas">

  <section class="card card-front" aria-label="Card front">
    <div class="front-logo">CUSHTANE</div>
    <div class="front-tagline">PROTECTIVE PACKAGING SOLUTIONS</div>
  </section>

  <section class="card card-back" aria-label="Card back">
    <div class="back-logo">CUSHTANE</div>
    <div class="back-tagline">PROTECTIVE PACKAGING SOLUTIONS</div>

    <div class="company-name">Cushtane Pty Ltd</div>
    <div class="person-name">Dara Oyelaran</div>
    <div class="person-title">General Manager</div>

    <ul class="contact-lines">
      <li>
        <svg viewBox="0 0 24 24" aria-label="Telephone"><path d="M6.6 10.8a15.2 15.2 0 0 0 6.6 6.6l2.2-2.2a1 1 0 0 1 1-.25 11.4 11.4 0 0 0 3.6.57 1 1 0 0 1 1 1V20a1 1 0 0 1-1 1A17 17 0 0 1 3 4a1 1 0 0 1 1-1h3.5a1 1 0 0 1 1 1c0 1.250.2 2.450.57 3.57a1 1 0 0 1-.25 1z"/></svg>
        02 9471 5826
      </li>
      <li>
        <svg viewBox="0 0 24 24" aria-label="Mobile"><path d="M7 2h10a2 2 0 0 1 2 2v16a2 2 0 0 1-2 2H7a2 2 0 0 1-2-2V4a2 2 0 0 1 2-2zm0 3v13h10V5z"/></svg>
        0438 217 564
      </li>
      <li>
        <svg viewBox="0 0 24 24" aria-label="Fax"><path d="M7 2h10v5H7zM4 8h16a2 2 0 0 1 2 2v7h-4v5H6v-5H2v-7a2 2 0 0 1 2-2zm4 9v3h8v-3z"/></svg>
        9471 5839
      </li>
    </ul>

    <div class="email">dara.oyelaran@cushtane.com.au</div>
    <div class="address">14 Larkin Road Kellwood NSW 2791</div>

    <div class="web-band">cushtane.com.au</div>
  </section>

</main>
</body>
</html>
```